Business Cards for a law firm

Business cards for our law firm. Use our silhoette logo and OAK PARTNERS - check our website (www.oakpartners.example)

Contact Information for Business Card

our silhouette logo, OAK PARTNERS, 800-555-0147, Dorian Pemberton, dorian@oakpartners.example

Requirements
Must have
• our silhouette logo, OAK PARTNERS, 800-555-0147, Dorian Pemberton, dorian@oakpartners.example

```html
<!DOCTYPE html>
<html lang="en">
<head>
<meta charset="utf-8">
<title>Oak Partners – Business Cards</title>
<link rel="stylesheet" href="https://fonts.googleapis.com/css2?family=Montserrat:wght@500&family=Open+Sans:wght@400;600&display=swap">
<style>
  :root {
    --bg: #1d1e21;
    --navy: #24347f;
    --navy-deep: #1c2a6b;
    --white: #ffffff;
    --soft: #d9def0;
  }
  html, body {
    margin: 0;
    padding: 0;
    width: 1200px;
    height: 900px;
    overflow: hidden;
    background: var(--bg);
  }
  .canvas {
    position: relative;
    width: 1200px;
    height: 900px;
  }
  .card {
    position: absolute;
    top: 290px;
    width: 560px;
    height: 320px;
    border-radius: 6px;
    overflow: hidden;
    background: linear-gradient(160deg, var(--navy) 0%, var(--navy-deep) 100%);
    box-shadow: 0 10px 30px rgba(0,0,0,.45);
  }
  .card--front { left: 30px; }
  .card--back { left: 610px; }

  .card__feature {
    position: absolute;
    inset: 0;
  }
  .wordmark {
    font-family: "Montserrat", sans-serif;
    font-weight: 500;
    color: var(--white);
    letter-spacing: 0.14em;
    margin: 0;
    white-space: nowrap;
  }
  .card--front .wordmark {
    position: absolute;
    left: 44px;
    top: 32px;
    font-size: 20px;
  }
  .holder {
    position: absolute;
    left: 44px;
    top: 112px;
    font-family: "Open Sans", sans-serif;
    color: var(--white);
  }
  .holder__name {
    margin: 0;
    font-size: 21px;
    font-weight: 600;
  }
  .holder__role {
    margin: 2px 0 0;
    font-size: 12px;
    color: var(--soft);
  }
  .contact {
    list-style: none;
    margin: 26px 0 0;
    padding: 0;
    font-size: 13px;
    color: var(--soft);
  }
  .contact li {
    display: flex;
    align-items: center;
    gap: 8px;
    margin-bottom: 7px;
  }
  .contact svg {
    width: 11px;
    height: 11px;
    fill: var(--white);
  }

  .brand {
    position: absolute;
    left: 0;
    right: 0;
    top: 50%;
    transform: translateY(-50%);
    display: flex;
    justify-content: center;
    align-items: center;
    gap: 18px;
  }
  .brand__dot {
    width: 30px;
    height: 30px;
    border-radius: 50%;
    background: var(--white);
  }
  .card--back .wordmark {
    font-size: 32px;
  }
</style>
</head>
<body>
<main class="canvas">
  <section class="card card--front">
    <svg class="card__feature" viewBox="0 0 560 320" width="560" height="320" role="img" aria-label="Two standing figures of the firm's partners in navy on a white field">
      <path d="M410 0 C352 40 330 130 334 190 C338 250 362 296 384 320 L560 320 L560 0 Z" fill="#ffffff"/>
    </svg>
    <p class="wordmark">OAK PARTNERS</p>
    <div class="holder">
      <p class="holder__name">Dorian Pemberton</p>
      <p class="holder__role">Lawyer</p>
      <ul class="contact">
        <li>
          <svg viewBox="0 0 24 24"><path d="M6.6 10.8a15.1 15.1 0 0 0 6.6 6.6l2.2-2.2a1 1 0 0 1 1-.25 11.4 11.4 0 0 0 3.6.57 1 1 0 0 1 1 1V20a1 1 0 0 1-1 1A17 17 0 0 1 3 4a1 1 0 0 1 1-1h3.5a1 1 0 0 1 1 1c0 1.25.2 2.45.57 3.57a1 1 0 0 1-.25 1z"/></svg>
          800-555-0147
        </li>
        <li>
          <svg viewBox="0 0 24 24"><path d="M2 5h20v14H2z M3.5 6.5 12 13l8.5-6.5" fill="none" stroke="#fff" stroke-width="2.2"/></svg>
          dorian@oakpartners.example
        </li>
        <li>
          <svg viewBox="0 0 24 24"><circle cx="12" cy="12" r="9" fill="none" stroke="#fff" stroke-width="2.2"/><path d="M3 12h18M12 3c3 3 3 15 0 18M12 3c-3 3-3 15 0 18" fill="none" stroke="#fff" stroke-width="1.8"/></svg>
          www.oakpartners.example
        </li>
      </ul>
    </div>
  </section>

  <section class="card card--back">
    <div class="brand">
      <span class="brand__dot"></span>
      <p class="wordmark">OAK PARTNERS</p>
    </div>
  </section>
</main>
</body>
</html>
```